Laser Tattoo Removal Business Cards

We are looking for a professional business card design for a laser tattoo removal business. Ideally looking for a black business card design. The name of the business is Palewick Tattoo Removal. We place our cards at local tattoo shops so we ideally are looking for something trendy/edgy to draw both male and female clientele in.

Target Market(s)

Male/Female ages 18-60

Contact Information for Business Card

black background ideally.. hoping to stay within greys, whites and black

Font styles to use
Serif
Sans Serif

Colors
121212
a9a9a9
5c5c5c
f5f5f5
ffffff
7f7f7f
606060
848484
9d9d9d

Requirements
Must have
• Employee Info:
• Melissa Thornbury
• Chief Executive Offer
• m: 919.537.2846
• w: 919.362.4178
• f: 919.685.3907
• mthornbury@palewicktattooremoval.example
• Address:
• 4615 Oakmere Pkwy, Suite 210
• Raleigh, NC 27654
• Website:
• www.palewicktattooremoval.example
Nice to have
• Myabe business name on back or logo on back and employee info on the front

```html
<!DOCTYPE html>
<html lang="en">
<head>
<meta charset="utf-8">
<title>Palewick Tattoo Removal – Business Cards</title>
<link href="https://fonts.googleapis.com/css2?family=Lato:wght@300;400;700&display=swap" rel="stylesheet">
<style>
  :root {
    --stage: #1c1c1c;
    --card-dark: #121212;
    --card-light: #ffffff;
    --ink-light: #f5f5f5;
    --ink-dark: #121212;
    --grey-mid: #5c5c5c;
  }
  * { margin: 0; padding: 0; box-sizing: border-box; }
  html, body { width: 1200px; height: 900px; overflow: hidden; }
  body {
    background: var(--stage);
    font-family: "Lato", sans-serif;
    position: relative;
  }
  .card {
    position: absolute;
    width: 620px;
    height: 354px;
    border-radius: 14px;
    box-shadow: 0 10px 30px rgba(0,0,0,0.5);
    overflow: hidden;
  }
  .card--front { left: 80px; top: 80px; background: var(--card-dark); color: var(--ink-light); }
  .card--back  { left: 500px; top: 466px; background: var(--card-light); color: var(--ink-dark); }

  .wordmark { text-align: center; font-weight: 400; text-transform: uppercase; color: inherit; }
  .wordmark__name { font-size: 54px; letter-spacing: 6px; line-height: 1; }
  .wordmark__tag {
    font-size: 19px; letter-spacing: 5px; margin-top: 18px;
    display: flex; align-items: center; justify-content: center; gap: 12px;
  }
  .wordmark__tag::before, .wordmark__tag::after {
    content: ""; width: 22px; height: 1px; background: currentColor;
  }
  .card--front .wordmark { position: absolute; top: 96px; left: 0; right: 0; }
  .website {
    position: absolute; bottom: 42px; left: 0; right: 0;
    text-align: center; font-size: 15px; letter-spacing: 2px; font-weight: 300;
  }

  .card--back .wordmark { position: absolute; top: 32px; right: 34px; width: 300px; }
  .card--back .wordmark__name { font-size: 34px; letter-spacing: 4px; }
  .card--back .wordmark__tag { font-size: 13px; letter-spacing: 3px; margin-top: 12px; }

  .person { position: absolute; left: 44px; top: 118px; }
  .person__name { font-size: 17px; font-weight: 300; line-height: 1.2; }
  .person__name strong { font-weight: 700; }
  .person__title { font-size: 12px; color: var(--grey-mid); margin-top: 3px; }

  .address { position: absolute; left: 44px; top: 182px; font-size: 14px; font-weight: 700; line-height: 1.45; }

  .contacts { position: absolute; left: 44px; top: 246px; list-style: none; font-size: 14px; }
  .contacts li { display: flex; align-items: center; gap: 12px; height: 22px; }
  .contacts svg { width: 14px; height: 14px; fill: var(--ink-dark); flex: none; }
</style>
</head>
<body>
  <section class="card card--front" aria-label="Card front">
    <div class="wordmark">
      <div class="wordmark__name">Palewick</div>
      <div class="wordmark__tag">Tattoo Removal</div>
    </div>
    <p class="website">www.palewicktattooremoval.example</p>
  </section>

  <section class="card card--back" aria-label="Card back">
    <div class="wordmark">
      <div class="wordmark__name">Palewick</div>
      <div class="wordmark__tag">Tattoo Removal</div>
    </div>
    <div class="person">
      <p class="person__name">Melissa <strong>Thornbury</strong></p>
      <p class="person__title">Chief Executive Offer</p>
    </div>
    <p class="address">4615 Oakmere Pkwy, Suite 210<br>Raleigh, NC 27654</p>
    <ul class="contacts">
      <li>
        <svg viewBox="0 0 16 16" aria-hidden="true"><path d="M2 5c0-2 2-3 6-3s6 1 6 3v1h-3V5H5v1H2zM4 7h8l2 6H2z"/></svg>
        919.537.2846
      </li>
      <li>
        <svg viewBox="0 0 16 16" aria-hidden="true"><path d="M4 1l3 3-2 2c1 2 3 4 5 5l2-2 3 3-2 3C7 15 1 9 1 3z"/></svg>
        919.362.4178
      </li>
      <li>
        <svg viewBox="0 0 16 16" aria-hidden="true"><path d="M4 1h8v4H4zM1 6h14v6h-3v3H4v-3H1zM5 10v3h6v-3z"/></svg>
        919.685.3907
      </li>
      <li>
        <svg viewBox="0 0 16 16" aria-hidden="true"><path d="M1 3h14v10H1zM2 4l6 5 6-5v1L8 10 2 5z" fill-rule="evenodd"/></svg>
        mthornbury@palewicktattooremoval.example
      </li>
    </ul>
  </section>
</body>
</html>
```